Custom Seed Packet design for Flower Farm

We need a design for our seeds packets.
The design will be a kind of "fill in the blanks" as we need the design to be adaptable for multiple varieties of seed. We will be using the design for a rubber stamp.
Our seed packets are 90x90mm in size.
Black logo only. No colour required.
A vintage botanical influence is desired.
Will need to include the following info,
"Wrenfield Gable Co logo" , "Seeds", "Plant Type", "Variety", "Harvested"

```html
<!DOCTYPE html>
<html lang="en">
<head>
<meta charset="utf-8">
<title>Seed Packet Stamp – Wrenfield Gable Co Flower Farm</title>
<link rel="stylesheet" href="https://fonts.googleapis.com/css2?family=Caveat+Brush&display=swap">
<style>
  :root {
    --paper: #d8c3a0;
    --ink: #1e1a16;
    --ornament-tint: rgba(30, 26, 22, 0.10);
  }
  * { margin: 0; padding: 0; box-sizing: border-box; }
  html, body {
    width: 1122px;
    height: 1200px;
    overflow: hidden;
    background: var(--paper);
  }
  .packet-stamp {
    position: relative;
    width: 1122px;
    height: 1200px;
    font-family: "Caveat Brush", cursive;
    color: var(--ink);
  }
  .ornate-frame {
    position: absolute;
    left: 63px;
    top: 115px;
    width: 996px;
    height: 970px;
  }
  .frame-band { fill: var(--ornament-tint); }
  .frame-inner-fill { fill: var(--paper); }
  .frame-line {
    fill: none;
    stroke: var(--ink);
    stroke-width: 3;
  }
  .frame-line--thin { stroke-width: 1.6; }

  .field {
    position: absolute;
    left: 200px;
    width: 700px;
    height: 60px;
  }
  .field-label {
    position: absolute;
    left: 0;
    bottom: 4px;
    font-size: 42px;
    line-height: 1;
  }
  .field-line {
    position: absolute;
    left: 253px;
    right: 0;
    bottom: 0;
    height: 2px;
    background: var(--ink);
  }
  .field--seeds { top: 309px; }
  .field--type { top: 377px; }
  .field--variety { top: 448px; }
  .field--harvested { top: 517px; }

  .farm-name {
    position: absolute;
    left: 560px;
    top: 790px;
    width: 330px;
    text-align: right;
    line-height: 1;
  }
  .farm-name__company {
    display: block;
    font-size: 26px;
  }
  .farm-name__title {
    display: block;
    font-size: 60px;
    margin-top: 4px;
  }
</style>
</head>
<body>
  <main class="packet-stamp">
    <svg class="ornate-frame" viewBox="0 0 996 970" role="img"
         aria-label="Vintage botanical scroll frame with flourishes and small rosebuds">
      <defs>
        <path id="frame-outline"
              d="M60 120 Q60 60 120 60
                 C250 60 300 110 400 110 C450 110 470 70 498 70 C526 70 546 110 596 110
                 C696 110 746 60 876 60 Q936 60 936 120
                 C936 300 900 350 900 485 C900 620 936 670 936 850
                 Q936 910 876 910
                 C746 910 696 860 596 860 C546 860 526 900 498 900 C470 900 450 860 400 860
                 C300 860 250 910 120 910 Q60 910 60 850
                 C60 670 96 620 96 485 C96 350 60 300 60 120 Z"/>
      </defs>
      <use href="#frame-outline" class="frame-band"/>
      <use href="#frame-outline" class="frame-inner-fill"
           transform="translate(498 485) scale(0.94) translate(-498 -485)"/>
      <use href="#frame-outline" class="frame-line"/>
      <use href="#frame-outline" class="frame-line frame-line--thin"
           transform="translate(498 485) scale(0.94) translate(-498 -485)"/>
    </svg>

    <div class="field field--seeds">
      <span class="field-label">Seeds</span>
      <span class="field-line"></span>
    </div>
    <div class="field field--type">
      <span class="field-label">Plant Type</span>
      <span class="field-line"></span>
    </div>
    <div class="field field--variety">
      <span class="field-label">Variety</span>
      <span class="field-line"></span>
    </div>
    <div class="field field--harvested">
      <span class="field-label">Harvested</span>
      <span class="field-line"></span>
    </div>

    <div class="farm-name">
      <span class="farm-name__company">Wrenfield Gable Co.</span>
      <span class="farm-name__title">Flower Farm</span>
    </div>
  </main>
</body>
</html>
```